Dorwin's Coating & Renewal Letterhead Design We want to revamp out old traditional letterhead with the new logo designs that are attached. We are working on getting all our company items from vehicles, business, cards, t-shirts, letterhead to match. This should include company colors, fonts, and flow of items that we have attached below.

Industry/Entity Type

Construction Company

Font styles to use
Sans Serif
Other font styles liked:
• Bold with outline

Colors
ec1f27
ffffff

Requirements
Must have
• Company Name: Dorwin's Coating & Renewal
• Address: 4728 SW 81st Ter Halverd cove fl 39417
• Office Number: (555) 413-2986
• Email: Dorwinrenewal@mailbrook.example
• License Number: KRT8046392
Nice to have
• Company Colors: red, white, black, and grey

```html
<!DOCTYPE html>
<html lang="en">
<head>
<meta charset="utf-8">
<title>Dorwin's Coating &amp; Renewal — Letterhead</title>
<link rel="stylesheet" href="https://fonts.googleapis.com/css2?family=Montserrat:wght@400;500;700;800&display=swap">
<style>
  :root {
    --brand-red: #ec1f27;
    --accent-orange: #ee4a22;
    --ink: #333333;
    --swoosh-grey: #e4e4e4;
    --rule-grey: #e6e6e6;
    --paper: #ffffff;
    --backdrop: #e6e6e6;
  }
  * { box-sizing: border-box; margin: 0; padding: 0; }
  html, body {
    width: 1200px; height: 1200px; overflow: hidden;
    background: var(--backdrop);
    font-family: "Montserrat", sans-serif;
    color: var(--ink);
  }
  .stage { position: relative; width: 1200px; height: 1200px; }
  .letterhead {
    position: absolute;
    left: 197px; top: 30px;
    width: 1089px; height: 1540px;
    background: var(--paper);
    transform: scale(0.74);
    transform-origin: top left;
    overflow: hidden;
  }
  .decor { position: absolute; inset: 0; width: 1089px; height: 1540px; }
  .brand-name {
    position: absolute; left: 65px; top: 70px;
    font-weight: 800; font-size: 44px; line-height: 52px;
    color: var(--brand-red); letter-spacing: 0.5px;
  }
  .license {
    position: absolute; right: 67px; top: 152px;
    font-weight: 700; font-size: 22px; letter-spacing: 0.3px;
    white-space: nowrap;
  }
  .divider {
    position: absolute; left: 153px; top: 274px;
    width: 1px; height: 1027px; background: var(--rule-grey);
  }
  .contact-rail {
    position: absolute;
    left: -437px; top: 772px;
    width: 1030px; height: 30px;
    transform: rotate(-90deg);
    display: flex; align-items: center; justify-content: space-between;
    font-weight: 700; font-size: 20px; letter-spacing: 0.1px;
    white-space: nowrap;
  }
  .contact-item { display: flex; align-items: center; gap: 12px; flex: none; white-space: nowrap; }
  .contact-icon { width: 26px; height: 26px; transform: rotate(90deg); flex: none; }
  .rail-dash { width: 20px; height: 2px; background: var(--accent-orange); transform: rotate(90deg); flex: none; }
  .signoff {
    position: absolute; left: 204px; top: 306px;
  }
  .signoff .closing { font-size: 18px; font-weight: 400; }
  .signoff .signer { font-size: 32px; font-weight: 700; margin-top: 18px; line-height: 34px; letter-spacing: 0.5px; }
  .signoff .role { font-size: 22px; font-weight: 700; line-height: 26px; }
  .letter-body {
    position: absolute; left: 204px; top: 588px; width: 840px;
    font-size: 18.3px; line-height: 35.8px; font-weight: 400;
    white-space: nowrap;
  }
  .letter-body p { margin-bottom: 35.8px; }
  .letter-body p.gap-lg { margin-bottom: 72px; }
  .address {
    position: absolute; left: 65px; top: 1420px;
    font-weight: 700; font-size: 22px; line-height: 26px; letter-spacing: 0.3px;
    white-space: nowrap;
  }
</style>
</head>
<body>
<div class="stage">
  <div class="letterhead">
    <svg class="decor" viewBox="0 0 1089 1540" aria-hidden="true">
      <rect class="top-rule" x="0" y="29" width="1089" height="4" fill="var(--brand-red)"/>
      <path class="swoosh-grey" d="M0,343 Q620,300 938,0 L1040,0 Q720,320 0,358 Z" fill="var(--swoosh-grey)"/>
      <path class="swoosh-grey" d="M645,273 Q900,210 1089,100 L1089,37 Q900,180 645,273 Z" fill="var(--swoosh-grey)"/>
      <path class="swoosh-orange" d="M247,1540 Q400,1460 639,1416 Q480,1460 338,1540 Z" fill="var(--accent-orange)"/>
      <path class="swoosh-orange" d="M636,1540 Q820,1460 1089,1412 L1089,1414 Q880,1465 738,1540 Z" fill="var(--accent-orange)"/>
    </svg>

    <div class="brand-name">Dorwin's Coating<br>&amp; Renewal</div>
    <div class="license">License Number: KRT8046392</div>

    <div class="divider"></div>

    <div class="contact-rail">
      <div class="contact-item">
        <svg class="contact-icon" viewBox="0 0 26 26"><circle cx="13" cy="13" r="11.5" fill="none" stroke="var(--accent-orange)" stroke-width="1.6"/><path d="M9.5 8.5c.8-.6 1.4-.3 1.8.5l.7 1.5c.2.6 0 1-.5 1.4l-.5.4c.6 1.4 1.6 2.4 2.9 3l.4-.5c.4-.5.9-.7 1.4-.5l1.5.7c.8.4 1 1 .5 1.8-.8 1.2-2.1 1.4-3.4.8-2.5-1.1-4.300-3-5.3-5.4-.5-1.3-.3-2.6.5-3.2z" fill="var(--accent-orange)"/></svg>
        <span>(555) 413-2986</span>
      </div>
      <div class="rail-dash"></div>
      <div class="contact-item">
        <svg class="contact-icon" viewBox="0 0 26 26"><circle cx="13" cy="13" r="11.5" fill="none" stroke="var(--accent-orange)" stroke-width="1.6"/><rect x="7.5" y="9" width="11" height="8" rx="1" fill="none" stroke="var(--accent-orange)" stroke-width="1.5"/><path d="M7.8 9.5 13 13.5l5.2-4" fill="none" stroke="var(--accent-orange)" stroke-width="1.5"/></svg>
        <span>Dorwinrenewal@mailbrook.example</span>
      </div>
      <div class="rail-dash"></div>
      <div class="contact-item">
        <svg class="contact-icon" viewBox="0 0 26 26"><circle cx="13" cy="13" r="11.5" fill="none" stroke="var(--accent-orange)" stroke-width="1.6"/><circle cx="13" cy="13" r="6" fill="none" stroke="var(--accent-orange)" stroke-width="1.3"/><path d="M7 13h12M13 7c-2.5 3-2.5 9 0 12M13 7c2.5 3 2.5 9 0 12" fill="none" stroke="var(--accent-orange)" stroke-width="1.1"/></svg>
        <span>www.dorwinsrenewal.example</span>
      </div>
    </div>

    <div class="signoff">
      <div class="closing">Sincearly,</div>
      <div class="signer">MARLO KEATS</div>
      <div class="role">Director</div>
    </div>

    <div class="letter-body">
      <p class="gap-lg" style="margin-bottom:35.8px">This is a sample letter that has been placed to demonstrate typing remat (Your Company).<br>
      letterhead design. When positioned properly, it will serve to work in harmony with all other<br>
      elements letterhead. This letterhead design is meant to project an image<br>
      This letterhead design is meant project an image of professionalism reliability. By using<br>
      simple aligen we have created a very spacious feeling. The simplicity suggest &nbsp;renglththe<br>
      spaciousnes contributes haesthetics the layout. These basic qualities along with the<br>
      (Your Company)</p>
      <p class="gap-lg">look and helps reinforce the (Your Company) brand. letterhead design is meant to project<br>
      an image design. When positioned properly, it will serve to work in harmony all the other<br>
      elements letterhead. sionalism and reliability.</p>
      <p>This letterhead design is based on the (Form of your logo) form (Your Company) logo.<br>
      Each stationery we have created a very spacious feeling. The simplicity suggests strength<br>
      the spaciousnes contribute part of the (Form of your logo).<br>
      This letterhead design is based on the (Form of your logo) form (Your Company) logo.<br>
      Each stationery we have created a very spacious feeling. The simplicity suggests strength<br>
      the spaciousnes contribute part of the (Form of your logo).</p>
    </div>

    <div class="address">4728 SW 81st Ter Halverd<br>cove fl 39417</div>
  </div>
</div>
</body>
</html>
```